Corvane Property Care Email Marketing Design

Dear Designer,
We're in need of an email background template for our company, Corvane Property Care, that reflects our commitment to building lasting relationships with our clients and providing top-quality restoration and cleaning services.
We'd like the template to incorporate our brand colors, which are #F2F2F3, #005EA5, #468ECC, and #000000, and to feature images related to our services, such as water restoration, emergency flood response, mold remediation, trauma scene clean-up, fire restoration, carpet cleaning, and more. Our logo and tagline, "Disaster Undone", should be prominently displayed in a unique and visually appealing way, along with our website address, www.corvanepropertycare-demo.net.
The email should be professional and positive, highlighting the camaraderie and teamwork among our employees. We want to thank our clients for their business, offer a special discount, and promote our services. The final design should be visually stunning and memorable, with a clear call-to-action to encourage clients to take advantage of the discount.
We'd like the final design in JPG or PNG format, with a resolution of at least 720x720 pixels.
Thank you for considering this project. We're excited to see what you come up with!
Best regards,
Tomas

```html
<!DOCTYPE html>
<html lang="en">
<head>
<meta charset="utf-8">
<title>Corvane Property Care – Disaster Undone</title>
<link rel="stylesheet" href="https://fonts.googleapis.com/css2?family=Playfair+Display:wght@600;700&family=Montserrat:wght@600;700&display=swap">
<style>
  :root {
    --sky-light: #d6eaf9;
    --sky: #a8d3f6;
    --brand-blue: #005ea5;
    --title-blue: #0d4c9e;
    --band-dark: #0a52ad;
    --band-light: #468ecc;
    --button-blue: #0b6fcd;
    --text-grey: #666a70;
    --white: #ffffff;
    --photo-dark: #2a2621;
    --photo-mid: #4d463e;
    --photo-tan: #8a7868;
    --photo-concrete: #9c9a96;
    --photo-shirt: #8e99a6;
  }
  * { margin: 0; padding: 0; box-sizing: border-box; }
  html, body { width: 1200px; height: 1200px; overflow: hidden; }
  body { background: var(--sky-light); }
  .email-card {
    position: relative;
    width: 1200px; height: 1200px;
    overflow: hidden;
    background: linear-gradient(120deg, var(--sky-light) 0%, #c4e2f9 50%, var(--sky) 100%);
    font-family: "Montserrat", sans-serif;
  }
  .brand-name {
    position: absolute; left: 84px; top: 112px;
    font-family: "Playfair Display", serif;
    font-weight: 700; font-size: 30px;
    color: var(--brand-blue);
    display: flex; align-items: center; gap: 12px;
  }
  .brand-name .brand-dot {
    width: 18px; height: 18px; border-radius: 50%;
    background: var(--brand-blue);
  }
  .tagline {
    position: absolute;
    font-family: "Playfair Display", serif;
    font-weight: 700; font-size: 88px; line-height: 1;
    color: var(--title-blue);
    text-shadow: 4px 6px 8px rgba(0, 40, 100, 0.3);
    letter-spacing: 1px;
  }
  .tagline-top { left: 84px; top: 236px; }
  .tagline-bottom { left: 162px; top: 350px; }
  .services-heading {
    position: absolute; left: 83px; top: 486px;
    font-family: "Playfair Display", serif;
    font-weight: 600; font-size: 29px;
    color: var(--title-blue);
  }
  .services-rule {
    position: absolute; left: 83px; top: 540px;
    width: 181px; height: 4px; background: var(--button-blue);
  }
  .service-list { list-style: none; position: absolute; left: 84px; top: 565px; }
  .service-list li {
    display: flex; align-items: center; gap: 12px;
    height: 30px; margin-bottom: 23px;
    font-weight: 700; font-size: 19px; color: var(--text-grey);
  }
  .service-list svg { width: 25px; height: 25px; flex: none; }
  .view-all {
    position: absolute; left: 84px; top: 798px;
    width: 208px; height: 59px; border-radius: 30px;
    background: var(--button-blue);
    color: var(--white); font-weight: 700; font-size: 21px;
    display: flex; align-items: center; justify-content: center;
    box-shadow: 2px 8px 14px rgba(0, 60, 140, 0.35);
  }
  .photo-mosaic, .contact-bands { position: absolute; left: 0; top: 0; width: 1200px; height: 1200px; }
  .call-block { position: absolute; left: 86px; top: 988px; display: flex; align-items: center; gap: 34px; }
  .call-block svg { width: 88px; height: 88px; }
  .call-label { font-weight: 700; font-size: 26px; color: var(--white); }
  .call-number { font-weight: 700; font-size: 37px; color: var(--white); margin-top: 12px; }
  .website {
    position: absolute; left: 665px; top: 1108px;
    display: flex; align-items: center; gap: 22px;
    font-weight: 700; font-size: 20.5px; color: var(--brand-blue);
  }
  .website svg { width: 28px; height: 28px; }
</style>
</head>
<body>
<main class="email-card">

  <div class="brand-name"><span class="brand-dot"></span>Corvane Property Care</div>

  <h1>
    <span class="tagline tagline-top">DISASTER</span>
    <span class="tagline tagline-bottom">UNDONE</span>
  </h1>

  <h2 class="services-heading">Our Services</h2>
  <div class="services-rule"></div>
  <ul class="service-list">
    <li><svg viewBox="0 0 24 24" fill="none" stroke="#468ecc" stroke-width="1.8" stroke-linecap="round" stroke-linejoin="round"><path d="M21 11.1V12a9 9 0 1 1-5.3-8.2"/><path d="M21 4 12 13l-3-3"/></svg>Water Restoration</li>
    <li><svg viewBox="0 0 24 24" fill="none" stroke="#468ecc" stroke-width="1.8" stroke-linecap="round" stroke-linejoin="round"><path d="M21 11.1V12a9 9 0 1 1-5.3-8.2"/><path d="M21 4 12 13l-3-3"/></svg>Emergency Flood Response</li>
    <li><svg viewBox="0 0 24 24" fill="none" stroke="#468ecc" stroke-width="1.8" stroke-linecap="round" stroke-linejoin="round"><path d="M21 11.1V12a9 9 0 1 1-5.3-8.2"/><path d="M21 4 12 13l-3-3"/></svg>Mold Remediation</li>
    <li><svg viewBox="0 0 24 24" fill="none" stroke="#468ecc" stroke-width="1.8" stroke-linecap="round" stroke-linejoin="round"><path d="M21 11.1V12a9 9 0 1 1-5.3-8.2"/><path d="M21 4 12 13l-3-3"/></svg>Trauma Scene Clean-up</li>
  </ul>

  <div class="view-all">VIEW ALL</div>

  <svg class="photo-mosaic" viewBox="0 0 1200 1200" role="img" aria-label="Photo mosaic: a worker in a hard hat and gloves shovelling debris inside a damaged building">
    <defs>
      <linearGradient id="sceneDepth" x1="0" y1="84" x2="0" y2="1003" gradientUnits="userSpaceOnUse">
        <stop offset="0" stop-color="var(--photo-dark)"/>
        <stop offset="0.55" stop-color="var(--photo-mid)"/>
        <stop offset="0.78" stop-color="#6e6860"/>
        <stop offset="1" stop-color="var(--photo-concrete)"/>
      </linearGradient>
      <linearGradient id="wallTone" x1="0" y1="334" x2="0" y2="921" gradientUnits="userSpaceOnUse">
        <stop offset="0" stop-color="var(--photo-tan)"/>
        <stop offset="0.45" stop-color="#6a5d50"/>
        <stop offset="0.62" stop-color="var(--photo-dark)"/>
        <stop offset="1" stop-color="var(--photo-concrete)"/>
      </linearGradient>
      <radialGradient id="workerGlow" cx="830" cy="560" r="190" gradientUnits="userSpaceOnUse">
        <stop offset="0" stop-color="var(--photo-shirt)" stop-opacity="0.85"/>
        <stop offset="1" stop-color="var(--photo-shirt)" stop-opacity="0"/>
      </radialGradient>
      <clipPath id="tiles">
        <rect x="715" y="157" width="159" height="162" rx="6"/>
        <rect x="715" y="327" width="159" height="163" rx="6"/>
        <rect x="715" y="496" width="159" height="164" rx="6"/>
        <rect x="715" y="669" width="159" height="334" rx="6"/>
        <rect x="884" y="84" width="232" height="235" rx="6"/>
        <rect x="884" y="327" width="158" height="333" rx="6"/>
        <rect x="884" y="669" width="232" height="164" rx="6"/>
        <rect x="1050" y="327" width="66" height="163" rx="6"/>
        <rect x="1050" y="496" width="66" height="164" rx="6"/>
        <rect x="535" y="661" width="81" height="90" rx="6"/>
        <rect x="535" y="758" width="170" height="163" rx="6"/>
      </clipPath>
      <clipPath id="wallTiles">
        <rect x="623" y="334" width="82" height="83" rx="6"/>
        <rect x="623" y="426" width="82" height="160" rx="6"/>
        <rect x="623" y="594" width="82" height="157" rx="6"/>
      </clipPath>
    </defs>
    <g clip-path="url(#tiles)">
      <rect x="535" y="84" width="581" height="919" fill="url(#sceneDepth)"/>
      <rect x="535" y="84" width="581" height="919" fill="url(#workerGlow)"/>
    </g>
    <g clip-path="url(#wallTiles)">
      <rect x="623" y="334" width="82" height="417" fill="url(#wallTone)"/>
    </g>
  </svg>

  <svg class="contact-bands" viewBox="0 0 1200 1200" aria-hidden="true">
    <path d="M0 1135 H508 V1000 H540 Q575 1000 590 1035 L660 1200 H0 Z" fill="var(--band-light)"/>
    <path d="M0 936 H450 Q476 936 488 962 L567 1135 H0 Z" fill="var(--band-dark)"/>
  </svg>

  <div class="call-block">
    <svg viewBox="0 0 64 64" fill="none" aria-hidden="true">
      <path d="M14 6c3-2 6-1 8 2l5 8c1 3 0 5-2 7l-3 2c2 6 8 13 15 16l2-3c2-2 4-3 7-2l8 5c3 2 4 5 2 8l-3 4c-3 3-8 4-12 2C24 50 12 38 7 24 5 19 6 13 10 10z" fill="#ffffff"/>
      <path d="M38 10a16 16 0 0 1 16 16" stroke="#ffffff" stroke-width="4" stroke-linecap="round"/>
      <path d="M38 2a24 24 0 0 1 24 24" stroke="#ffffff" stroke-width="4" stroke-linecap="round"/>
    </svg>
    <div>
      <div class="call-label">Call Us</div>
      <div class="call-number">(555) 014-2290</div>
    </div>
  </div>

  <div class="website">
    <svg viewBox="0 0 24 24" fill="none" aria-hidden="true">
      <circle cx="12" cy="12" r="10" fill="#005ea5"/>
      <g stroke="#c4e2f9" stroke-width="1.2">
        <ellipse cx="12" cy="12" rx="4.5" ry="10"/>
        <path d="M2 12h20M4 7h16M4 17h16M12 2v20"/>
      </g>
    </svg>
    <span>www.corvanepropertycare-demo.net</span>
  </div>

</main>
</body>
</html>
```